PTV Website

We need a completely new modern design for our website www.ptv.org.au.

The Keyholders Alliance League of Australia Inc is a non-profit, volunteer-run association representing owners of strata-titled residential developments. We provide education, information and lobbying to improve the management of apartment complexes and the lives of those living in them. We’re all about “owners helping owners”. More information on our organisation can be seen at www.ptv.org.au.

Our new logo (from a recent PixelHarbor contest) is attached.

Target Market(s)

Primary audience - Owners of residential apartments - both resident owners and investor owners
Secondary audiences – current and potential sponsors; organisations providing products & services to Owners Corporations & Body Corporates

Industry/Entity Type

Non-Profit

Number of Pages Required

3 pages

Requirements
Must have
• We need:
- A design for the home page
- A design for 2-column content pages
- Fonts and colours for
* standard text
* H1, H2, H3 and H4 heading tags
* Bulleted and numbered lists
- A complementary colour scheme for the Calendar page
- A complementary breadcrumb format
- A standard format to display the associated tags for any content page

The above are described in more detail in the attached document.

The design should:
- be modern, uncluttered and clean
- reflect a sense of community, coupled with authority, professionalism and knowledge
- be a fixed width of 1000px

At a minimum the files we need are:
- The source file (PSD with all component layers is preferred, but not mandatory)
- JPG preview files
- Any stand-alone images as a PNG with transparent backgrounds
- Details of all fonts and sizes used (if they can’t be easily identified in the source files)

Note: The site is built with the Drupal CMS, so all page elements must be able to be clearly isolated.
Should not have
• Any fonts that are not freely available

```html
<!DOCTYPE html>
<html lang="en">
<head>
<meta charset="utf-8">
<title>PTV Website</title>
<link href="https://fonts.googleapis.com/css2?family=Arimo:wght@400;700&display=swap" rel="stylesheet">
<style>
:root{
  --gold:#d89f2a;
  --gold-dark:#b9821a;
  --gold-light:#e9b84a;
  --blue:#0b3fbf;
  --blue-bright:#0a55e8;
  --heading:#1c3fa6;
  --link:#1b2e98;
  --text:#333;
  --sheet:#f3f3f3;
  --box:#e9e9e9;
  --box-border:#d4d4d4;
  --rule:#111;
}
*{box-sizing:border-box;margin:0;padding:0}
html,body{width:1200px;height:4162px;overflow:hidden;background:#fff}
body{position:relative;font-family:"Arimo",Arial,sans-serif;color:var(--text)}
.page{position:absolute;left:0;width:1200px}
.sheet{position:absolute;left:16px;top:0;width:1172px;bottom:0;background:var(--sheet)}
.page-rule{position:absolute;left:0;width:1200px;height:4px;background:var(--rule)}
.abs{position:absolute}

/* header */
.brand{position:absolute;left:40px;top:14px;display:flex;align-items:center;gap:22px}
.brand-mark{width:96px;height:96px;background:var(--gold)}
.brand-name{font-size:33px;line-height:31px;letter-spacing:2px;color:#1d2f78;font-weight:400}
.search{position:absolute;left:752px;top:40px;width:432px;height:92px;background:#fff;display:flex;align-items:center;padding-left:10px;gap:12px}
.search-field{width:282px;height:28px;border:1px solid #ddd;background:#fff}
.search-btn{width:88px;height:26px;background:var(--blue-bright);color:#fff;font-size:19px;text-align:center;line-height:26px}
.nav{position:absolute;left:24px;top:158px;width:1156px;height:68px;background:linear-gradient(var(--gold-light),var(--gold) 45%,var(--gold-dark));border-bottom:5px solid #c48a1e;display:flex;align-items:center;padding-left:10px}
.nav a{color:#fff;text-decoration:none;font-size:24px;padding:0 16px;border-left:1px solid rgba(255,255,255,.35);line-height:40px;text-shadow:0 1px 1px rgba(0,0,0,.25)}
.nav a:first-child{border-left:none}
.crumbs{position:absolute;left:24px;top:232px;width:1156px;height:34px;background:#e6e6e6;border-top:3px solid var(--gold);font-size:12px;font-weight:700;color:var(--link);padding:11px 0 0 18px}
.crumbs .sep{display:inline-block;width:7px;height:7px;background:var(--gold);margin:0 4px 0 10px}
.footer{position:absolute;left:24px;width:1156px;height:66px;background:linear-gradient(var(--gold),var(--gold-dark));color:#fff;font-size:14px;font-weight:700;text-align:center;line-height:66px;letter-spacing:.5px}

/* headings + text */
.h-side{font-size:21px;color:var(--heading);font-weight:400}
.h-main{font-size:28px;color:var(--heading);font-weight:400;letter-spacing:-.5px}
.h-article{font-size:20px;color:var(--heading);font-weight:400;letter-spacing:.4px}
.copy{font-size:14.5px;line-height:17px;color:#444}
.copy p+p{margin-top:17px}
.box{position:absolute;background:var(--box);border:3px solid var(--box-border)}
.dots{position:absolute;width:0;border-left:2px dotted #c89a3a}

/* login */
.field-label{font-size:13px;font-weight:700;color:#333;margin-top:12px}
.field{width:218px;height:27px;background:#fff;border:1px solid #ddd;margin-top:6px}
.login-btn{display:inline-block;background:var(--blue);color:#fff;font-size:16px;padding:4px 16px;margin-top:8px}
.small-link{font-size:12px;font-weight:700;margin-top:12px}

/* topic list */
.topics{list-style:none;padding:14px 10px}
.topics li{font-size:12.5px;font-weight:700;color:#222;margin-bottom:15px;display:flex;align-items:center;gap:10px}
.topics li::before{content:"";width:9px;height:9px;background:var(--blue);flex:none}

/* news */
.news-title{font-size:15px;color:var(--link);font-weight:700;text-decoration:underline}
.news-meta{font-size:12px;color:var(--blue);font-weight:700;margin:14px 0 18px}
.more{display:inline-block;background:var(--gold);color:#222;font-size:12px;font-weight:700;padding:3px 6px;margin-top:14px;border:1px solid #b6801a}
.read-more{font-size:13px;font-weight:700;color:#222;text-decoration:underline}

/* article list */
.articles{list-style:none}
.articles li{font-size:13px;font-weight:700;color:var(--link);display:flex;gap:14px;margin-bottom:16px;letter-spacing:.6px;line-height:15px}
.articles li::before{content:"";width:9px;height:9px;background:var(--gold);flex:none;margin-top:3px}

/* calendar */
.views{position:absolute;left:909px;top:326px;width:230px;display:flex;justify-content:space-between;font-size:14px;font-weight:700;color:var(--link)}
.cal-bar{position:absolute;left:40px;top:347px;width:1099px;height:41px;background:var(--blue);color:#fff;font-size:14px;font-weight:700;display:flex;justify-content:space-between;align-items:center;padding:0 14px;border:2px solid #0a2d8c}
.cal{position:absolute;left:40px;top:392px;width:1099px;display:grid;grid-template-columns:160px 142px 143px 177px 165px 132px 180px;border:2px solid #d2d2d2}
.cal .dow{background:linear-gradient(var(--gold),var(--gold-dark));color:#fff;font-size:13px;font-weight:700;text-align:center;height:32px;line-height:32px;border-right:1px solid #fff}
.cal .day{background:var(--box);border-right:2px solid #fff;border-bottom:2px solid #fff;position:relative}
.cal .num{position:absolute;right:4px;top:2px;min-width:34px;height:20px;background:#3a63d8;color:#fff;font-size:13px;font-weight:700;text-align:center;line-height:20px}
.event-pop{position:absolute;left:493px;top:840px;width:323px;height:218px;background:var(--blue-bright);border:3px solid #0a2d8c;color:#fff;font-size:13px;font-weight:700;padding:10px 12px;line-height:16px}
.event-pop .badge{position:absolute;right:10px;top:38px;width:90px;height:72px;background:#fff}
.event-pop .close{position:absolute;right:10px;top:8px;font-size:20px}
</style>
</head>
<body>

<!-- PAGE 1: HOME -->
<section class="page" style="top:0;height:1400px">
  <div class="sheet"></div>
  <div class="brand"><div class="brand-mark"></div><div class="brand-name">KEYHOLDERS<br>ALLIANCE<br>LEAGUE</div></div>
  <div class="search"><div class="search-field"></div><div class="search-btn">Search</div></div>
  <nav class="nav"><a>Home</a><a>About</a><a>News</a><a>Events</a><a>Membership</a><a>Sponsorship</a><a>Links</a><a>Contact</a><a>Members Only</a></nav>

  <div class="abs" style="left:24px;top:229px;width:795px;height:210px;background:linear-gradient(var(--blue-bright),var(--blue) 60%,#0a34a6);border-bottom:5px solid var(--gold);color:#fff;padding:46px 0 0 22px">
    <div style="font-size:24px;line-height:40px"><span style="font-size:32px">Owners</span> Helping Owners</div>
    <div style="font-size:24px;line-height:40px"><span style="font-size:32px">Representing</span> Strata Title Residential Developments</div>
    <div style="font-size:24px;line-height:40px"><span style="font-size:32px">Lobbying and Sharing</span> Information to Improve Apartment Living</div>
  </div>
  <div class="abs" role="img" aria-label="Photo of a smiling couple receiving keys to their new apartment" style="left:822px;top:232px;width:356px;height:300px;background:linear-gradient(135deg,#f0f0f0,#c8b8a0 55%,#6d7f92);border:6px solid #fff;box-shadow:0 6px 12px rgba(0,0,0,.3)"></div>

  <h3 class="h-side abs" style="left:37px;top:498px">Member Login</h3>
  <div class="box" style="left:37px;top:533px;width:262px;height:210px;padding:6px 15px">
    <div class="field-label">Username or e-mail: *</div><div class="field"></div>
    <div class="field-label">Password: *</div><div class="field"></div>
    <div class="login-btn">LOGIN</div>
    <div class="small-link">Request new password</div>
  </div>
  <h3 class="h-side abs" style="left:37px;top:778px">Topic List</h3>
  <div class="box" style="left:37px;top:811px;width:262px;height:190px">
    <ul class="topics"><li>Lorem ipsum.</li><li>Dolor sit amet, consectetur.</li><li>Adipisicing elit, sed do.</li><li>Eiusmod tempor incididunt ut et.</li><li>Dolore magna aliqua.</li><li>Ut enim ad veniam, nostrud.</li></ul>
  </div>

  <div class="dots" style="left:317px;top:505px;height:770px"></div>
  <div class="dots" style="left:887px;top:505px;height:770px"></div>

  <h1 class="h-main abs" style="left:331px;top:503px">Featured Announcements</h1>
  <div class="copy abs" style="left:331px;top:545px;width:512px">
    <p>What happens when complaints get trampled underfoot. When is a bylaw not a bylaw? When the Residential Disputes Review Panel decides it doesn't really matter.</p>
    <p>Government reintroduce clamping and towing of illegally parked cars to stop protracted legal and sometimes physical disputes they say are turning apartment car parks into battle grounds</p>
  </div>
  <a class="read-more abs" style="left:753px;top:684px">Read More...</a>
  <h2 class="h-main abs" style="left:331px;top:715px">Recent News</h2>
  <div class="box" style="left:331px;top:759px;width:545px;height:477px;padding:30px 14px;background:linear-gradient(#f6f6f6,#e6e6e6);border-width:2px">
    <div class="news-title">Bye bye to bylaws</div>
    <div class="news-meta">Submitted by admin on 9 December 2009</div>
    <div class="copy" style="width:500px">What happens when complaints get trampled underfoot. When is a bylaw not a bylaw? When the Residential Disputes Review Panel decides it doesn't really matter, that's when</div>
    <div class="more">More...</div>
    <div class="news-title" style="margin-top:68px">Push to clamp illegal parkers</div>
    <div class="news-meta">Submitted by admin on 9 December 2009</div>
    <div class="copy" style="width:500px">RESIDENTS in flats and other strata buildings are demanding the State Government reintroduce clamping and towing of illegally parked cars to stop protracted legal and sometimes physical disputes they say are turning apartment car parks into battle grounds</div>
    <div class="more">More...</div>
  </div>

  <h3 class="h-side abs" style="left:901px;top:537px">Upcoming Events</h3>
  <div class="box" style="left:901px;top:568px;width:262px;height:186px;padding:16px 10px">
    <div class="copy" style="font-size:13px;line-height:16px"><p>Lorem ipsum dolor sit amet, ceius-mod tempor incididunt ut labore et.</p><p>Dolore magna aliqua. Ut enim ad minim veniam, quis nostrud.</p><p>ExDuis aute irure dolor in repre-henderit in voluptate.</p></div>
  </div>
  <h3 class="h-side abs" style="left:903px;top:786px">Recent Forum Posts</h3>
  <div class="box" style="left:901px;top:819px;width:262px;height:186px;padding:16px 10px">
    <div class="copy" style="font-size:13px;line-height:16px"><p>Lorem ipsum dolor sit amet, consectetur adipisicincididunt ut labore et.</p><p>Dolore magna aliqua. Ut enim ad minim veniam, quis nostrud.</p><p>Exercitation ullamcoe dolor in reprehenderit in voluptate.</p></div>
  </div>

  <footer class="footer" style="top:1297px">©Keyholders Alliance League Inc 2008 | Disclaimer | Contact Us</footer>
</section>

<div class="page-rule" style="top:1436px"></div>

<!-- PAGE 2: MEMBERS AREA -->
<section class="page" style="top:1442px;height:1344px">
  <div class="sheet"></div>
  <div class="brand"><div class="brand-mark"></div><div class="brand-name">KEYHOLDERS<br>ALLIANCE<br>LEAGUE</div></div>
  <div class="search"><div class="search-field"></div><div class="search-btn">Search</div></div>
  <nav class="nav"><a>Home</a><a>About</a><a>News</a><a>Events</a><a>Membership</a><a>Sponsorship</a><a>Links</a><a>Contact</a><a>Members Only</a></nav>
  <div class="crumbs">Home<span class="sep"></span>Members Area</div>

  <h3 class="abs" style="left:40px;top:296px;font-size:17px;font-weight:700;color:var(--heading)">Articles</h3>
  <ul class="articles abs" style="left:48px;top:340px;width:330px">
    <li>Building Managements Rights-<br>Buyers Beware</li>
    <li>Building Owners &amp; Occupiers-<br>How Up to date must they be (AS 1851)</li>
    <li>Deffects</li>
    <li>Demistifying High-Rise Fire Safety</li>
    <li>Executive Committees</li>
    <li>Fire Safety and the new standrds<br>( AS 1851-2005 )</li>
    <li>Insurance Tips For Stats Plan</li>
    <li>Noise</li>
    <li>Owners Corporation &amp; GST</li>
    <li>Serviced Appartments- A New Fom<br>Of Starta Abuse</li>
    <li>Smoke Alarms</li>
    <li>Strata Managers</li>
    <li>Which Way to Vote?<br>The Burden of Choice!</li>
  </ul>
  <h3 class="abs" style="left:40px;top:846px;font-size:16px;font-weight:700;color:var(--heading)">Topic List</h3>
  <div class="box" style="left:40px;top:872px;width:264px;height:189px">
    <ul class="topics"><li>Lorem ipsum.</li><li>Dolor sit amet, consectetur.</li><li>Adipisicing elit, sed do.</li><li>Eiusmod tempor incididunt ut et.</li><li>Dolore magna aliqua.</li><li>Ut enim ad veniam, nostrud.</li></ul>
  </div>
  <div class="dots" style="left:381px;top:298px;height:870px"></div>

  <article class="abs" style="left:404px;top:296px;width:760px">
    <h1 class="h-article">Building Managements Rights- Buyers Beware</h1>
    <div class="copy" style="margin-top:12px"><p>The Keyholders Alliance League of Australia (PTV) is the peak body representing apartment owners, with most members drawn from Owners Corporations' Executive Committees (ECs) or concerned apartment owners around Australia. PTV is a not-for-profit association.</p><p>Through representation, lobbying, information-sharing and networking, we perform a vital service for our members that supports them in living in and/or investing in strata titled property.</p><p>We lobby for changes necessary to Government policy and legislation, and sit on many Government and industry boards and panels to present our views to those in power. The PTV gives members a voice at both State and Federal levels, and an opportunity to put forward their views on problems, solutions and the kind of future that, as apartment owners, we'd all like to see.</p></div>
    <h2 class="h-article" style="margin-top:44px">Building Owners &amp; Occupiers- How Up to date must they be (AS 1851)</h2>
    <div class="copy" style="margin-top:10px"><p>The PTV educates EC members and individuals by sharing experiences and disseminating information from relevant sources and related organisations.</p><p>Regular meetings, seminars and an online discussion group give members access to fellow members' experiences in areas such as defects rectification, strata disputes, shared services, and levy management. These resources may save members thousands of dollars and an immense amount of heartache in the long run!</p></div>
    <h3 class="h-article" style="margin-top:56px">Deffects</h3>
    <div class="copy" style="margin-top:8px"><p>Regular meetings, seminars and an online discussion group give members access to fellow members' experiences in areas such as defects rectification, strata disputes, shared services, and levy management. These resources may save members thousands of dollars and an immense amount of heartache in the long run!</p></div>
    <h4 class="h-article" style="margin-top:56px">Demistifying High-Rise Fire Safety</h4>
    <div class="copy" style="margin-top:8px"><p>Regular meetings, seminars and an online discussion group give members access to fellow members' experiences in areas such as defects rectification, strata disputes, shared services, and levy management. These resources may save members thousands of dollars and an immense amount of heartache in the long run!</p></div>
  </article>

  <footer class="footer" style="top:1223px">©Keyholders Alliance League Inc 2008 | Disclaimer | Contact Us</footer>
</section>

<div class="page-rule" style="top:2784px"></div>

<!-- PAGE 3: EVENTS CALENDAR -->
<section class="page" style="top:2790px;height:1332px">
  <div class="sheet"></div>
  <div class="brand"><div class="brand-mark"></div><div class="brand-name">KEYHOLDERS<br>ALLIANCE<br>LEAGUE</div></div>
  <div class="search"><div class="search-field"></div><div class="search-btn">Search</div></div>
  <nav class="nav"><a>Home</a><a>About</a><a>News</a><a>Events</a><a>Membership</a><a>Sponsorship</a><a>Links</a><a>Contact</a><a>Members Only</a></nav>
  <div class="crumbs">Home<span class="sep"></span>Events</div>

  <h1 class="abs" style="left:39px;top:306px;font-size:19px;font-weight:400;color:var(--heading)">Events</h1>
  <div class="views"><span>Year</span><span>Month</span><span>Week</span><span>Day</span></div>
  <div class="cal-bar"><span>« Prev</span><span>January 2010</span><span>Next »</span></div>
  <div class="cal">
    <div class="dow">Sunday</div><div class="dow">Monday</div><div class="dow">Tuesday</div><div class="dow">Wednesday</div><div class="dow">Thursday</div><div class="dow">Friday</div><div class="dow">Saturday</div>
    <div class="day" style="height:84px"></div><div class="day"></div><div class="day"></div><div class="day"></div><div class="day"></div><div class="day"><span class="num">1</span></div><div class="day"><span class="num">2</span></div>
    <div class="day" style="height:102px"><span class="num">3</span></div><div class="day"><span class="num">4</span></div><div class="day"><span class="num">5</span></div><div class="day"><span class="num">6</span></div><div class="day"><span class="num">7</span></div><div class="day"><span class="num">8</span></div><div class="day"><span class="num">9</span></div>
    <div class="day" style="height:90px"><span class="num">10</span></div><div class="day"><span class="num">11</span></div><div class="day"><span class="num">12</span></div><div class="day"><span class="num">13</span></div><div class="day"><span class="num">14</span></div><div class="day"><span class="num">15</span></div><div class="day"><span class="num">16</span></div>
    <div class="day" style="height:94px"><span class="num">17</span></div><div class="day"><span class="num">18</span></div><div class="day"><span class="num">19</span></div><div class="day"><span class="num">20</span></div><div class="day"><span class="num">21</span></div><div class="day"><span class="num">22</span></div><div class="day"><span class="num">23</span></div>
    <div class="day" style="height:100px"><span class="num">24</span></div><div class="day"><span class="num">25</span></div><div class="day"><span class="num">26</span></div><div class="day"><span class="num">27</span></div><div class="day"><span class="num">28</span></div><div class="day"><span class="num">29</span></div><div class="day"><span class="num">30</span></div>
    <div class="day" style="height:98px"><span class="num">31</span></div><div class="day"></div><div class="day"></div><div class="day"></div><div class="day"></div><div class="day"></div><div class="day"></div>
  </div>
  <div class="event-pop">
    <span class="close">✕</span>
    <div>SPI Consumer Awareness Seminar</div>
    <div class="badge"></div>
    <div style="margin-top:14px">Time: 24 February 2010<br>6:15pm - 7:45pm</div>
    <div style="margin-top:16px">Location:<br>Harbourline Conference Centre<br>48 Quarry Lane</div>
    <div style="margin-top:16px">Sydney<br>Organiser: Strata Practice<br>Institute</div>
  </div>

  <footer class="footer" style="top:1250px">©Keyholders Alliance League Inc 2008 | Disclaimer | Contact Us</footer>
</section>

<div class="page-rule" style="top:4128px"></div>
</body>
</html>
```